Vennekamp.dk - FellowCup

I need a design for a WordPress site that serves to inform and present the national golfchampionship for colleagues in Denmark. The sites need to be visual stuninng or big, and it doesnt have a lot of pages. Maybe 5-6 regular text pages and not a lot of navigation. It should be a simple and powerfull site.

The sites need to present and sell the tournament, and have a clear call to action button "Sign up" (Tilmeld) and resultscoring.

If you can make a logo and visual ID for the tournament as well that would be a bonus.

Target Market(s)

Golfers

Logo Text

Vennekamp

Number of Pages Required

3 page

Requirements
Must have
• A frontpage
• Button 1 - Tilmeld (danish for sign up)
• Button 2 - Resultater (results)
Nice to have
• Logo
• A style we can use offline as well

```html
<!DOCTYPE html>
<html lang="da">
<head>
<meta charset="utf-8">
<title>Vennekamp 2015 – Dansk Kontoridræt Forbund</title>
<link href="https://fonts.googleapis.com/css2?family=Open+Sans:wght@300;400;600;700&display=swap" rel="stylesheet">
<style>
:root{
  --red:#c3202f;
  --red-dark:#9e1622;
  --blue:#1c7fbf;
  --blue-dark:#145f93;
  --navy:#0e3a63;
  --green:#1d8a3a;
  --text:#3a3a3a;
  --muted:#8a8a8a;
  --line:#e2e2e2;
  --grey-bg:#efefef;
  --footer:#2b2b2b;
  --white:#fff;
}
*{box-sizing:border-box;margin:0;padding:0}
html,body{width:1200px;height:2812px;overflow:hidden}
body{font-family:"Open Sans",Arial,sans-serif;color:var(--text);background:var(--white);position:relative;font-size:13px;line-height:1.6}
.abs{position:absolute}

/* header */
.site-header{left:0;top:0;width:1200px;height:155px;background:var(--white)}
.brand{left:100px;top:60px;display:flex;align-items:center;gap:14px}
.brand-dot{width:32px;height:32px;border-radius:50%;background:var(--blue)}
.brand-name{font-size:22px;font-weight:600;color:#1f2a36}
.cta{top:66px;height:38px;width:118px;border-radius:3px;color:#fff;font-size:13px;display:flex;align-items:center;justify-content:center;box-shadow:inset 0 -3px 0 rgba(0,0,0,.2)}
.cta-signup{left:850px;background:var(--red)}
.cta-results{left:980px;background:var(--blue)}

.main-nav{left:0;top:155px;width:1200px;height:50px;background:linear-gradient(var(--blue),var(--blue-dark))}
.main-nav ul{position:absolute;left:100px;top:0;display:flex;list-style:none;height:50px}
.main-nav li{color:#fff;font-size:12.5px;padding:0 19px;line-height:50px}
.main-nav li.active{background:var(--red)}
.nav-search{left:1048px;top:155px;width:52px;height:50px;background:var(--red);display:flex;align-items:center;justify-content:center}

/* hero */
.hero{left:0;top:205px;width:1200px;height:460px;background:linear-gradient(180deg,#4f7a3a 0%,#3e6b2b 45%,#2e5520 100%)}
.hero-title{left:0;top:455px;width:1200px;text-align:center;color:#fff;font-size:40px;font-weight:300;letter-spacing:1px}
.hero-title b{font-weight:700}
.hero-rule{left:485px;top:445px;width:230px;height:2px;background:rgba(255,255,255,.8)}
.hero-arrow{top:380px}

.finder{left:128px;top:640px;width:944px;height:50px;background:#fff;border:2px solid var(--red);box-shadow:0 8px 14px rgba(0,0,0,.15);display:flex;align-items:center;padding-left:20px;gap:12px}
.finder-label{font-size:12px;color:#444;width:160px}
.finder-field{height:32px;border:1px solid #d5d5d5;font-size:12px;color:#777;padding:0 10px;display:flex;align-items:center;justify-content:space-between}
.finder-btn{position:absolute;right:-2px;top:-2px;width:110px;height:50px;background:var(--red);color:#fff;font-size:16px;font-weight:600;display:flex;align-items:center;justify-content:center}

/* tabs */
.tabs{left:100px;top:730px;width:1000px;height:60px;display:flex}
.tabs div{flex:1;color:#fff;font-size:13px;display:flex;align-items:center;justify-content:center}
.tab-red{background:var(--red)}.tab-navy{background:var(--navy)}.tab-blue{background:var(--blue)}.tab-green{background:var(--green)}
.intro-panel{left:100px;top:790px;width:1000px;height:528px;border:1px solid var(--line);border-top:none;background:#fff}

.side-box{background:#fff;border:1px solid var(--line)}
.side-head{background:linear-gradient(var(--blue),var(--blue-dark));color:#fff;font-size:15px;padding:0 22px;height:50px;display:flex;align-items:center}
.side-list{list-style:none}
.side-list li{border-bottom:1px solid var(--line);padding:10px 14px 10px 22px;font-size:12px;display:flex;justify-content:space-between;align-items:center;min-height:40px}
.side-list li span.t::before{content:"›";color:#999;margin-right:12px}
.dot{width:12px;height:12px;border-radius:50%;background:#b9b9b9;flex:none;position:relative}
.dot::after{content:"";position:absolute;left:3px;top:3.5px;border-left:5px solid #fff;border-top:2.5px solid transparent;border-bottom:2.5px solid transparent}

.welcome{left:412px;top:830px;width:670px}
.welcome h1{font-size:22px;font-weight:400;color:#333;display:flex;align-items:center;gap:12px}
.welcome h1 i{width:40px;height:40px;border-radius:50%;background:var(--blue);display:block}
.welcome p{font-size:12px;line-height:1.95;margin-top:18px}
.video{left:412px;top:1010px;width:362px;height:270px;background:linear-gradient(180deg,#9bb3c9 0%,#7d9a6a 55%,#4d6d3a 100%)}
.video-bar{position:absolute;left:0;bottom:0;width:100%;height:28px;background:#1b1b1b}
.video-bar i{position:absolute;left:0;top:0;height:4px;width:68%;background:var(--red)}
.video-play{position:absolute;left:158px;top:105px;width:46px;height:32px;border-radius:7px;background:var(--red)}
.video-play::after{content:"";position:absolute;left:18px;top:9px;border-left:12px solid #fff;border-top:7px solid transparent;border-bottom:7px solid transparent}
.video-copy{left:788px;top:1010px;width:292px}
.video-copy h3{font-size:13px;font-weight:600;color:#333;text-transform:uppercase}
.video-copy p{font-size:12px;line-height:1.95}
.btn-more{left:788px;top:1232px;width:136px;height:42px;background:var(--red);border-radius:3px;color:#fff;font-size:12.5px;display:flex;align-items:center;justify-content:center}

/* event section */
.event-bg{left:0;top:1362px;width:1200px;height:1338px;background:var(--grey-bg)}
.info-box{left:100px;top:1400px;width:250px}
.doc-list li{padding:12px 14px 12px 18px}
.doc{display:flex;gap:12px;align-items:flex-start;font-size:12px;line-height:1.3}
.doc small{display:block;color:var(--muted);font-size:11px}
.pdf{width:16px;height:20px;background:#fff;border:1px solid #c9c9c9;border-top:4px solid var(--red);flex:none;margin-top:2px}
.contact-box{left:100px;top:1837px;width:250px}
.contact-photo{height:135px;background:linear-gradient(180deg,#bfc6cd,#6b717a)}
.contact-body{padding:16px 0 14px 0;font-size:12px;line-height:1.5;background:var(--grey-bg)}
.contact-body strong{font-weight:600;font-size:13px}
.contact-body .role{color:var(--muted);font-size:11.5px}
.partner-box{left:100px;top:2172px;width:250px;height:204px;background:#fff;border:1px solid var(--line);padding:18px 18px}
.partner-box .lbl{font-size:10.5px;color:#444}
.partner-name{font-weight:600;font-size:15px;color:#1a4a8a;margin-top:6px}
.partner-badge{width:60px;height:60px;border-radius:50%;background:#d9dfe6;margin:14px auto 0}
.partner-name2{font-weight:600;font-size:18px;color:#1a4a8a;text-align:center;margin-top:10px}

.event{left:390px;top:1392px;width:710px}
.event h1{font-size:22px;font-weight:400;color:#333;letter-spacing:.5px}
.event-photo{left:390px;top:1445px;width:360px;height:268px;background:linear-gradient(180deg,#c9d6e2 0%,#3e63a8 55%,#e8e8ee 100%);border:6px solid #fff}
.event-facts{left:776px;top:1445px;width:320px;font-size:12.5px}
.event-facts h2{font-size:13px;font-weight:700;color:#333;line-height:1.45;text-transform:uppercase}
.event-facts dt{font-weight:600;margin-top:12px}
.share{left:390px;top:1728px;display:flex;gap:4px}
.share i{width:24px;height:24px;display:block;border-radius:2px}
.s1{background:#3b5998}.s2{background:#2b6aa3}.s3{background:#7a8087}.s4{background:#f2b01e}.s5{background:#0e76a8}.s6{background:#e45a2a}
.event-body{left:390px;top:1762px;width:710px;font-size:11.5px;line-height:1.95}
.event-body .lead{font-size:13.5px;font-weight:600;color:#333;line-height:1.6}
.event-body h3{font-size:14px;font-weight:600;color:#333;margin-top:18px;line-height:1.5}

/* footer */
.site-footer{left:0;top:2700px;width:1200px;height:112px;background:var(--footer);color:#d8d8d8;font-size:12px}
.footer-links{position:absolute;left:100px;top:30px}
.footer-addr{position:absolute;left:100px;top:60px}
.footer-share{position:absolute;left:860px;top:44px;display:flex;gap:8px}
.footer-share i{width:32px;height:32px;display:block;border-radius:2px}
.footer-code{position:absolute;left:1141px;top:52px;font-size:11px;color:#aaa}
</style>
</head>
<body>

<header class="site-header abs">
  <div class="brand abs"><span class="brand-dot"></span><span class="brand-name">Dansk Kontoridræt Forbund</span></div>
  <a class="cta cta-signup abs">Tilmeld</a>
  <a class="cta cta-results abs">Resultater</a>
</header>

<nav class="main-nav abs">
  <ul>
    <li class="active">Om Dansk Kontoridræt Forbund</li>
    <li>Bliv medlem</li>
    <li>Magasinet KONTORIDRÆT</li>
    <li>Find forening</li>
    <li>Pressecenter</li>
    <li>Find person</li>
    <li>Min side</li>
  </ul>
</nav>
<div class="nav-search abs">
  <svg width="20" height="20" viewBox="0 0 20 20"><circle cx="8" cy="8" r="6" fill="none" stroke="#fff" stroke-width="2.5"/><line x1="12.5" y1="12.5" x2="18" y2="18" stroke="#fff" stroke-width="3"/></svg>
</div>

<section class="hero abs" role="img" aria-label="Golfkølle og bold på tee ved en spillers sko på fairway"></section>
<div class="hero-rule abs"></div>
<h1 class="hero-title abs">DANSK <b>KONTORIDRÆT</b> FORBUND</h1>
<svg class="hero-arrow abs" style="left:34px" width="20" height="60" viewBox="0 0 20 60"><polyline points="18,2 2,30 18,58" fill="none" stroke="#fff" stroke-width="1.5"/></svg>
<svg class="hero-arrow abs" style="left:1146px" width="20" height="60" viewBox="0 0 20 60"><polyline points="2,2 18,30 2,58" fill="none" stroke="#fff" stroke-width="1.5"/></svg>

<form class="finder abs">
  <span class="finder-label">Find Arrangement/Stævane</span>
  <span class="finder-field" style="width:198px">Søgeord</span>
  <span class="finder-field" style="width:198px">Vælg Komme <span>▾</span></span>
  <span class="finder-field" style="width:198px">Vælgtidspunkt <span>▾</span></span>
  <span class="finder-btn">Søg</span>
</form>

<div class="tabs abs">
  <div class="tab-red">Idræt og motion</div>
  <div class="tab-navy">Arrangementer og stævner</div>
  <div class="tab-blue">Sundhed på arbejdspladsen</div>
  <div class="tab-green">Foreningsnet</div>
</div>
<div class="intro-panel abs"></div>

<aside class="side-box abs" style="left:124px;top:828px;width:252px">
  <div class="side-head">Arrangementer og stævner</div>
  <ul class="side-list">
    <li><span class="t">Kontoridræt Open</span><i class="dot"></i></li>
    <li><span class="t">Cykel &amp; Løb Stafet</span><i class="dot"></i></li>
    <li><span class="t">Ekstrem Herredag</span><i class="dot"></i></li>
    <li><span class="t">Kontorernes<br>&nbsp;&nbsp;&nbsp;&nbsp;Motionsdag2015</span><i class="dot"></i></li>
    <li><span class="t">Eventyrløbet</span><i class="dot"></i></li>
    <li><span class="t">Vennekamp</span><i class="dot"></i></li>
    <li><span class="t">Teambold</span><i class="dot"></i></li>
    <li><span class="t">Nord Cup Fodbold</span><i class="dot"></i></li>
    <li style="border-bottom:none"><span class="t">Nord Cup Høvdingebold</span><i class="dot"></i></li>
  </ul>
</aside>

<article class="welcome abs">
  <h1><i></i>WELCOME TO DANSK KONTORIDRÆT FORBUND</h1>
  <p>Brænder du for cykling, fodbold, yoga - eller en helt anden idræt? Vil du gerne dyrke motion og styrke fællesskabet med dine kolleger? Læs hvordan du starter en forening på arbejdspladsen og får mulighed for at dyrke idræt med dine kolleger og andre, der brænder for idræt og fællesskabet omkring sport. Dansk Kontoridræt Forbund arbejder for at styrke foreningsidrætten lokalt på arbejdspladsen og i kontoridrætsforeningerne.</p>
</article>
<div class="video abs" role="img" aria-label="Videostillbillede af to golfspillere med golfvogne på banen">
  <span class="video-play"></span>
  <div class="video-bar"><i></i></div>
</div>
<div class="video-copy abs">
  <h3>Se video fra Vennekamp finalen 2011</h3>
  <p>&nbsp;&nbsp;Brænder du for cykling, fodbold, yoga - eller en helt anden idræt? Vil du gerne dyrke motion og styrke fællesskabet med dine kolleger? Læs hvordan du starter en forening på arbejdspladsen og får mulighed for at dyrke idræt med dine kolleger og andre, der brænder for idræt og fællesskabet omkring sport. Dansk Kontoridræt Forbund arbejder.Brænder du for cykling</p>
</div>
<a class="btn-more abs">View more info</a>

<div class="event-bg abs"></div>

<aside class="side-box info-box abs">
  <div class="side-head">Mere information</div>
  <ul class="side-list doc-list">
    <li><span class="doc"><i class="pdf"></i><span>Puljer<small>(PDF,203 KB)</small></span></span><i class="dot"></i></li>
    <li><span class="doc"><i class="pdf"></i><span>Turneringsplan<small>(PDF,203 KB)</small></span></span><i class="dot"></i></li>
    <li><span class="doc"><i class="pdf"></i><span>Turneringsbetingelser<small>(PDF,203 KB)</small></span></span><i class="dot"></i></li>
    <li><span class="doc"><i class="pdf"></i><span>Holdkaptajner<small>(PDF,203 KB)</small></span></span><i class="dot"></i></li>
    <li><span class="doc"><i class="pdf"></i><span>7_8_handicaptabel<small>(PDF,203 KB)</small></span></span><i class="dot"></i></li>
    <li style="border-bottom:none"><span class="doc"><i class="pdf"></i><span>Ofte stillede spørgsmål<small>(PDF,203 KB)</small></span></span><i class="dot"></i></li>
  </ul>
</aside>

<aside class="contact-box abs">
  <div class="side-head">Kontakt</div>
  <div class="contact-photo" role="img" aria-label="Portræt af generalsekretæren"></div>
  <div class="contact-body">
    <strong>Lars Holmgaard</strong><br>
    <span class="role">Generalsekretær</span><br>
    Tlf: 41 22 88 10<br>
    Mail: lho@kontoridraet.dk
  </div>
</aside>

<aside class="partner-box abs">
  <div class="lbl">I samarbejde med:</div>
  <div class="partner-name">Grøn Bane Samarbejde</div>
  <div class="partner-badge"></div>
  <div class="partner-name2">Søholt Rejser</div>
</aside>

<section class="event abs"><h1>VENNEKAMP 2015</h1></section>
<div class="event-photo abs" role="img" aria-label="Kolleger i blå trøjer samler hænderne i en holdcirkel"></div>
<dl class="event-facts abs">
  <h2>Danmarks sjoveste kollegaturnering i golf. Spil mod andre spillere på nye baner.</h2>
  <dt>Tidspunkt:</dt><dd>1. maj 2015 kl. 07:00 - 18. sep 2015 kl. 21:30</dd>
  <dt>Kontakt</dt><dd>Mette Vinther, Tlf. 65201430</dd>
  <dt>Tilmeldingsfrist:</dt><dd>27. april 2015</dd>
</dl>
<div class="share abs"><i class="s1"></i><i class="s2"></i><i class="s3"></i><i class="s4"></i><i class="s5"></i><i class="s6"></i></div>

<div class="event-body abs">
  <p class="lead">Turneringen afvikles i 2015 for 8. gang.Finalestævnet er i år på Lindely Golfklubs bane på Fyn.<br>Vær med, og vind rejsegavekort for hele holdet på op til kr. 22.000,- som 1. præmie, dog max. kr. 5.500, - pr. deltager, jf. amatørbestemmelsem</p>
  <h3>Pris</h3><p>Kr. 500,- pr. hold.</p>
  <h3>Deltagere</h3><p>Turneringen er åben for alle klubgolfere med gyldigt DGK-kort, gyldigt EGA handicap og amatørstatus.</p>
  <h3>Hold og puljer</h3><p>Et hold består af 2-4 spillere med to spillere fra holdet pr. match. Turneringen kører i puljer à 5-6 hold, som er delt op geografisk, efter hvor i landet I kommer fra. Puljens holdkaptajner aftaler selv indbyrdes tid og sted for den enkelte match - så I kan spille, hvor og hvornår det passer jer.<br>Alle betaler egen greenfee.</p>
  <h3>Spilleform</h3><p>Spilleformen er fourball - highflow hulspilsturnering, hvor 2 spillere fra holdet spiller med 2 spillere fra et andet hold.<br>Læs mere i turneringsbetingelserne, som du finder her på side</p>
  <h3>Stopdatoer</h3><p>Runde 1: 18. maj<br>Runde 2: 8. juni<br>Runde 3: 29. juni<br>Runde 4: 17. august<br>Runde 5: 7. september</p>
  <h3>Finalestævne fredag den 18. september 2015</h3><p>Vinderne fra hver pulje kvalificerer sig til at deltage i finalestævnet, som spilles på Lindely Golfklub, Skovbrynet 14, 5999 Lindely fredag den 18. september 2015 kl. 10.00.<br>Finalen bliver spillet som stableford four-ball best-ball med 7/8 handicap og med gunstart.<br>Finalestævnet spilles af to spillere fra hvert hold. Greenfee og middag betales af Dansk Kontoridræt Forbund</p>
  <h3>Præmier</h3><p>Puljevindernes præmie er deltagelse i finalestævnet.<br>Dansk Kontoridræt Forbund betaler greenfee, sportsbolle, vand og middag til finalestævnet.</p>
  <h3>Finalepræmie</h3><p>1. præmie: Et rejsegavekort på op til kr. 22.000,- pr. hold, dog max. kr. 5.500,- pr. tilmeldt spiller.<br>2. præmie: Et gavekort til golfudstyr på kr. 2000,- pr. hold.<br>3. præmie: Et gavekort til golfudstyr på kr. 1000,- pr. hold.</p>
  <p style="margin-top:18px">På finaledagen er der derudover præmie til længste drive og nærmest flaget.</p>
</div>

<footer class="site-footer abs">
  <div class="footer-links">Om Dansk Kontoridræt Forbund / Bliv medlem / Magasinet KONTORIDRÆT / Find forening / Pressecenter / Find person / Min side</div>
  <div class="footer-addr">Dansk Kontoridræt Forbund Havnegade 8 5999 Søholt Tlf. 65 40 22 10 kontakt@kontoridraet.dk</div>
  <div class="footer-share"><i class="s1"></i><i class="s2"></i><i class="s3"></i><i class="s4"></i><i class="s5"></i><i class="s6"></i></div>
  <div class="footer-code">C12</div>
</footer>

</body>
</html>
```